Maple Grove Schools | brand new stationery!

We need stationery design with our new logo! Our company updated it's name and image and we like to incorporate the new one on our stationery, business cards and email signature. We are looking for fresh, new ideas!
Industry: Childcare, Elementary and Middle School
Company Name: Maple Grove Schools
Tagline: Bright Futures Start Here
Main colors: Blue, white and a little yellow
Star shape is something new for us! Do you see a way to incorporate it as a design element?

```html
<!DOCTYPE html>
<html lang="en">
<head>
<meta charset="utf-8">
<title>Maple Grove Schools – Stationery</title>
<link rel="stylesheet" href="https://fonts.googleapis.com/css2?family=Poppins:wght@400;600&family=Roboto+Slab:wght@400;500&display=swap">
<style>
  :root {
    --bg: #dadada;
    --paper: #ffffff;
    --navy: #031a6e;
    --yellow: #fbc014;
    --ink: #1a1a1a;
    --edge: #3a3a3a;
  }
  * { box-sizing: border-box; margin: 0; padding: 0; }
  html, body { width: 1200px; height: 749px; overflow: hidden; background: var(--bg); }
  .canvas { position: relative; width: 1200px; height: 749px; background: var(--bg); }

  .piece { position: absolute; background: var(--paper); overflow: hidden; }
  .piece .wave { position: absolute; left: 0; top: 0; width: 100%; height: 100%; }

  .brand-name {
    font-family: "Poppins", sans-serif; font-weight: 600; color: var(--ink);
    text-align: center; line-height: 1.05; position: absolute;
  }
  .brand-name span { display: block; }

  .contact-list { list-style: none; font-family: "Roboto Slab", serif; color: var(--ink); position: absolute; }
  .contact-list li { display: flex; align-items: center; gap: 4px; }
  .contact-list svg { flex: none; }

  .address {
    position: absolute; font-family: "Roboto Slab", serif; font-weight: 500;
    color: var(--paper); white-space: nowrap;
  }

  /* Letterhead */
  .letterhead { left: 388px; top: 133px; width: 371px; height: 479px; border-right: 1px solid var(--edge); border-bottom: 1px solid var(--edge); }
  .letterhead .brand-name { left: 24px; top: 36px; font-size: 11px; }
  .letterhead .contact-divider { position: absolute; left: 250px; top: 10px; width: 1px; height: 26px; background: var(--navy); }
  .letterhead .contact-list { left: 257px; top: 10px; font-size: 6.6px; line-height: 8.7px; }
  .letterhead .address { right: 24px; top: 454px; font-size: 7.6px; }

  /* Business card */
  .business-card { left: 161px; top: 335px; width: 347px; height: 105px; border-right: 1px solid #bcbcbc; border-bottom: 1px solid #bcbcbc; }
  .business-card .holder { position: absolute; left: 18px; top: 20px; font-family: "Poppins", sans-serif; font-size: 8.8px; color: var(--navy); font-weight: 400; }
  .business-card .role { position: absolute; left: 18px; top: 32px; font-family: "Roboto Slab", serif; font-size: 6.6px; color: var(--ink); }
  .business-card .contact-list { left: 18px; top: 45px; font-size: 6.6px; line-height: 9px; }
  .business-card .brand-name { right: 22px; top: 43px; font-size: 13.5px; width: 120px; }
  .business-card .address { right: 12px; top: 91px; font-size: 6.9px; }

  /* Envelope */
  .envelope { left: 800px; top: 231px; width: 295px; height: 304px; background: transparent; overflow: visible; }
  .envelope .envelope-front { position: absolute; left: 0; top: 0; width: 295px; height: 148px; background: var(--paper); overflow: hidden; border-bottom: 1px solid #9a9a9a; }
  .envelope .envelope-back { position: absolute; left: 0; top: 156px; width: 295px; height: 148px; background: var(--paper); border-bottom: 1px solid var(--edge); overflow: hidden; }
  .envelope .brand-name { left: 12px; top: 30px; font-size: 8.3px; }
  .envelope .address { right: 20px; top: 134px; font-size: 6px; }
</style>
</head>
<body>
<main class="canvas">

  <!-- Letterhead -->
  <section class="piece letterhead" aria-label="Letterhead">
    <svg class="wave" viewBox="0 0 371 479" preserveAspectRatio="none" aria-hidden="true">
      <path fill="var(--yellow)" d="M0,415 C50,442 120,452 222,431 L222,433 C150,452 70,455 0,430 Z"/>
      <path fill="var(--navy)" d="M0,436 C60,458 125,460 205,441 C280,424 340,420 371,424 L371,479 L0,479 Z"/>
    </svg>
    <div class="brand-name"><span>Maple Grove</span><span style="font-weight:400">Schools</span></div>
    <div class="contact-divider"></div>
    <ul class="contact-list">
      <li><svg width="7" height="7" viewBox="0 0 10 10"><rect x="0.5" y="0.5" width="9" height="9" rx="1.5" fill="none" stroke="var(--navy)"/><path d="M3,2.5 L4.3,2.5 L4.6,4 L3.9,4.6 Q4.6,6 6,6.6 L6.5,5.8 L8,6.1 L8,7.4 Q4,7.8 3,2.5Z" fill="var(--navy)"/></svg>044-987 654 321</li>
      <li><svg width="7" height="7" viewBox="0 0 10 10"><rect x="0" y="1.5" width="10" height="7" fill="var(--navy)"/><path d="M0,1.5 L5,5.5 L10,1.5" fill="none" stroke="#fff" stroke-width="0.9"/></svg>hello@maplegrove.org</li>
      <li><svg width="7" height="7" viewBox="0 0 10 10"><circle cx="5" cy="5" r="4.4" fill="none" stroke="var(--navy)"/><ellipse cx="5" cy="5" rx="1.9" ry="4.4" fill="none" stroke="var(--navy)" stroke-width="0.8"/><path d="M0.6,5 H9.4 M1.4,3 H8.6 M1.4,7 H8.6" stroke="var(--navy)" stroke-width="0.7"/></svg>www.maplegroveschools.org</li>
    </ul>
    <p class="address">Your Address line goes here, Country Code 0123456</p>
  </section>

  <!-- Business card -->
  <section class="piece business-card" aria-label="Business card">
    <svg class="wave" viewBox="0 0 347 105" preserveAspectRatio="none" aria-hidden="true">
      <path fill="var(--yellow)" d="M0,69 C40,88 110,94 205,79 L205,80 C120,97 50,96 0,83 Z"/>
      <path fill="var(--navy)" d="M0,85 C40,101 100,104 170,90 C240,76 300,71 347,72 L347,105 L0,105 Z"/>
    </svg>
    <p class="holder">Clara Whitfield</p>
    <p class="role">Managing Director</p>
    <ul class="contact-list">
      <li><svg width="7" height="7" viewBox="0 0 10 10"><rect x="0.5" y="0.5" width="9" height="9" rx="1.5" fill="none" stroke="var(--navy)"/><path d="M3,2.5 L4.3,2.5 L4.6,4 L3.9,4.6 Q4.6,6 6,6.6 L6.5,5.8 L8,6.1 L8,7.4 Q4,7.8 3,2.5Z" fill="var(--navy)"/></svg>044-987 654 321</li>
      <li><svg width="7" height="7" viewBox="0 0 10 10"><rect x="0" y="1.5" width="10" height="7" fill="var(--navy)"/><path d="M0,1.5 L5,5.5 L10,1.5" fill="none" stroke="#fff" stroke-width="0.9"/></svg>hello@maplegrove.org</li>
      <li><svg width="7" height="7" viewBox="0 0 10 10"><circle cx="5" cy="5" r="4.4" fill="none" stroke="var(--navy)"/><ellipse cx="5" cy="5" rx="1.9" ry="4.4" fill="none" stroke="var(--navy)" stroke-width="0.8"/><path d="M0.6,5 H9.4 M1.4,3 H8.6 M1.4,7 H8.6" stroke="var(--navy)" stroke-width="0.7"/></svg>www.maplegroveschools.org</li>
    </ul>
    <div class="brand-name"><span>Maple Grove</span><span style="font-weight:400">Schools</span></div>
    <p class="address">Your Address line here, Country Code 0123456</p>
  </section>

  <!-- Envelope -->
  <section class="piece envelope" aria-label="Envelope">
    <div class="envelope-front">
      <svg class="wave" viewBox="0 0 295 148" preserveAspectRatio="none" aria-hidden="true">
        <path fill="var(--yellow)" d="M0,121 C40,137 100,141 153,125 L153,126 C100,144 40,145 0,131 Z"/>
        <path fill="var(--navy)" d="M0,133 C35,145 80,145 135,134 C190,122 240,117 270,121 C285,124 292,128 295,131 L295,148 L0,148 Z"/>
      </svg>
      <div class="brand-name"><span>Maple Grove</span><span style="font-weight:400">Schools</span></div>
      <p class="address">Your Address line here, Country Code 0123456</p>
    </div>
    <div class="envelope-back">
      <svg class="wave" viewBox="0 0 295 148" preserveAspectRatio="none" aria-hidden="true">
        <path fill="var(--navy)" d="M0,0 L295,0 L284,35 L11,35 Z"/>
      </svg>
    </div>
  </section>

</main>
</body>
</html>
```